Pediatric Therapy Clinic Brochure

We need a Brochure for a new pediatric therapy clinic. The clinic offers occupational therapy, physical therapy, speech therapy and feeding therapy. We want a brochure for parents, doctors and medical professional. It should have a fun and inviting, but still professional feel. Should be kid focused, bright and colorful. All the text / wording is there and a rough layout. Now I need someone to tidy and jazz it up and make it look professional.

Target Market(s)

Parents, doctors, medical professional

Industry/Entity Type

Medical

Font styles to use
Serif
Sans Serif

Requirements
Must have
• Keep All the text with information about services the same. Logo on front. Pictures throughout (use any of the pictures provided) (try and match up with corresponding service) (pictures are labeled). Need to have Map and contact info
• Keep colors consistent with our logo
Nice to have
• Background, special effects. Make it look fancy and professional
Should not have
• Not so busy that is takes away from the text

```html
<!DOCTYPE html>
<html lang="en">
<head>
<meta charset="utf-8">
<title>Brightpath Pediatric Therapy – Brochure Inside</title>
<link href="https://fonts.googleapis.com/css2?family=Oswald:wght@500;600&family=Arimo:wght@400;700&display=swap" rel="stylesheet">
<style>
  :root{
    --bg:#3a3232;
    --paper:#f4f4f6;
    --blue:#1b5a9e;
    --orange:#e8731f;
    --orange-text:#e25a1c;
    --yellow:#e8c41c;
    --ink-blue:#1d4f92;
  }
  *{box-sizing:border-box;margin:0;padding:0}
  html,body{width:1200px;height:1200px;overflow:hidden;background:var(--bg)}
  body{font-family:"Arimo",Arial,sans-serif;position:relative}
  .brochure{
    position:absolute;left:40px;top:160px;width:1120px;height:866px;
    display:flex;background:var(--paper);box-shadow:0 20px 40px rgba(0,0,0,.45);
  }
  .panel{
    position:relative;flex:1;padding:64px 30px 40px;display:flex;flex-direction:column;
    overflow:hidden;
  }
  .panel + .panel{border-left:1px solid #dcdce2}
  .top-banner{
    position:absolute;top:0;left:0;width:100%;height:28px;
    background:linear-gradient(90deg,var(--blue) 0%,var(--orange) 50%,var(--blue) 100%);
    opacity:.9;
  }
  .base-band{position:absolute;left:0;bottom:0;width:100%;height:22px;background:var(--yellow)}
  .photo-frame{
    border:9px solid var(--orange);border-radius:22px;overflow:hidden;height:168px;
    box-shadow:0 3px 8px rgba(0,0,0,.25);
  }
  .photo{width:100%;height:100%}
  .photo--painted-hands{background:linear-gradient(135deg,#f2e7de 0%,#e8c9b4 45%,#d9453c 70%,#f0eae6 100%)}
  .photo--whispering-kids{background:linear-gradient(120deg,#f3ded0 0%,#d8b08a 40%,#9d6a4c 70%,#4a5468 100%)}
  .service{text-align:center}
  .service h2{
    font-family:"Oswald",sans-serif;font-weight:600;color:var(--blue);
    font-size:27px;letter-spacing:.2px;line-height:1.1;text-transform:uppercase;
  }
  .service .lede{color:var(--ink-blue);font-size:13.5px;line-height:1.35;margin:4px 8px 0}
  .rule{height:3px;background:var(--blue);margin:10px 0 12px}
  .points{list-style:none;text-align:left;color:var(--orange-text);font-weight:700;font-size:14.5px;line-height:1.3}
  .points li{padding-left:14px;position:relative}
  .points li::before{content:"•";position:absolute;left:0;color:var(--orange-text)}
  .points--compact{font-size:13px}
  .gap{margin-top:18px}
  .logo{margin-top:auto;margin-bottom:40px;display:flex;align-items:center;justify-content:center;gap:8px}
  .logo-dot{width:14px;height:14px;border-radius:50%;background:var(--orange);flex:none}
  .logo-name{font-weight:700;font-size:20px;color:var(--blue);line-height:1;white-space:nowrap}
  .coming-soon{position:absolute;right:0;bottom:0;width:240px;height:220px}
  .coming-soon p{
    position:absolute;right:16px;bottom:60px;width:120px;text-align:center;
    font-size:13px;color:#3b2f12;line-height:1.25;
  }
</style>
</head>
<body>
<main class="brochure">

  <section class="panel panel--occupational">
    <div class="top-banner" role="img" aria-label="Decorative blue and orange pennant banner"></div>
    <div class="photo-frame"><div class="photo photo--painted-hands" role="img" aria-label="Photo of a smiling boy showing paint-covered hands"></div></div>
    <div class="service gap">
      <h2>Occupational Therapy</h2>
      <p class="lede">Helping children build better self-esteem, confidence and independence in all the things they do.</p>
      <div class="rule"></div>
      <ul class="points">
        <li>Sensory Processing Disorder</li>
        <li>Balance, Coordination, Strength, and Endurance</li>
        <li>Fine Motor and Handwriting</li>
        <li>Visual- Motor Integration</li>
        <li>Play and Social Skills</li>
        <li>Feeding and Oral Motor Skills</li>
        <li>Self-Care</li>
        <li>Academic and Cognitive Skills</li>
        <li>Behavioral Difficulties</li>
        <li>Developmental Delays</li>
      </ul>
    </div>
    <div class="photo-frame" style="margin-top:auto;margin-bottom:22px"><div class="photo photo--whispering-kids" role="img" aria-label="Photo of three young children whispering and smiling"></div></div>
    <div class="base-band"></div>
  </section>

  <section class="panel panel--speech">
    <div class="top-banner" role="img" aria-label="Decorative blue and orange pennant banner"></div>
    <div class="service">
      <h2>Speech Therapy</h2>
      <p class="lede">Helping children speak, communicate and understand language.</p>
      <div class="rule"></div>
      <ul class="points points--compact">
        <li>Expressive and Receptive Language</li>
        <li>Speech and Language Developmental Milestones</li>
        <li>Articulation / Intelligibility</li>
        <li>Speech Fluency</li>
        <li>Pragmatics and Social Skills</li>
        <li>Literacy and Vocabulary</li>
        <li>Apraxia of Speech</li>
        <li>Augmentative and Alternative Communication</li>
        <li>Feeding and Oral Motor</li>
      </ul>
    </div>
    <div class="service gap">
      <h2>Sensory Integration</h2>
      <p class="lede">Gradually increasing play based activities to improve a child's nervous system. Helping children learn to self-regulate their emotions, behaviors and arousal levels.</p>
      <div class="rule"></div>
      <ul class="points points--compact">
        <li>Autism and ADHD</li>
        <li>Sensory Processing Disorder</li>
        <li>Poor Tolerance of Sensory Stimuli from the Environment</li>
        <li>Meltdowns and Tantrums</li>
        <li>Poor Balance/Body Awareness</li>
        <li>Poor Attention and Concentration</li>
        <li>Poor Self-Regulation</li>
        <li>Behavior and Social Difficulties</li>
        <li>Poor Motor Coordination and Motor Planning</li>
        <li>Aggression, Frustration or Avoidance Behaviors</li>
      </ul>
    </div>
    <div class="logo">
      <span class="logo-dot" aria-hidden="true"></span>
      <span class="logo-name">Brightpath Pediatric Therapy</span>
    </div>
    <div class="base-band"></div>
  </section>

  <section class="panel panel--feeding">
    <div class="top-banner" role="img" aria-label="Decorative blue and orange pennant banner"></div>
    <div class="service">
      <h2>Feeding Therapy</h2>
      <p class="lede">Providing skilled assessment and intervention to children with feeding difficulties.</p>
      <div class="rule"></div>
      <ul class="points points--compact">
        <li>Food Aversions</li>
        <li>Food Refusal</li>
        <li>Very Picky Eating</li>
        <li>Avoidance of Certain Textures</li>
        <li>Gagging and Vomiting</li>
        <li>Oral Motor/ Chewing Difficulties</li>
        <li>Limited Diet/Food Repertoire</li>
      </ul>
    </div>
    <div class="service gap">
      <h2>Physical Therapy</h2>
      <p class="lede">Helping children move and interact within their environment smoothly and confidently.</p>
      <div class="rule"></div>
      <ul class="points points--compact">
        <li>Torticollis</li>
        <li>Walking and Mobility</li>
        <li>Developmental Motor Milestones</li>
        <li>Balance, Coordination, Motor Planning</li>
        <li>Strength, Muscle Tone and Range of Motion</li>
        <li>Sports Injuries</li>
        <li>Toe Walking</li>
        <li>Myofascial Release</li>
        <li>Postural Control and Positioning</li>
      </ul>
    </div>
    <div class="service gap">
      <h2>Group Therapy</h2>
      <p class="lede">Using peer role models to learn new and challenging skills.</p>
      <div class="rule"></div>
      <ul class="points points--compact">
        <li>Social Groups</li>
        <li>Feeding Groups</li>
      </ul>
    </div>
    <div class="coming-soon">
      <svg width="240" height="220" viewBox="0 0 240 220" aria-hidden="true" style="position:absolute;inset:0">
        <polygon points="240,0 240,220 0,220" fill="#e8c41c"/>
      </svg>
      <p>**More Group Classes Coming Soon</p>
    </div>
  </section>

</main>
</body>
</html>
```